iPhone iOS 7 App For Managing Tasks/Photos for Internal Company Use

We need an app design that displays company objectives and task, and provides the interface for employees to complete a task by uploading a photo and adding comments.

Please see attached mock up sketches as a rough guideline

Final delivery of files must contain PSD, and all layers/objects sliced both is PSD and PNG files

Target Market(s)

This is a tool for internal employee use

Industry/Entity Type

It Company

Requirements
Must have
• Must include logo, and match the colour scheme
Use iPhone iOS 7 Style

```html
<!DOCTYPE html>
<html lang="en">
<head>
<meta charset="utf-8">
<title>Objectives</title>
<link href="https://fonts.googleapis.com/css2?family=Arimo:wght@400;500&family=Roboto+Condensed:wght@300&display=swap" rel="stylesheet">
<style>
  :root {
    --page-bg: #f1f3f5;
    --bar-dark: #5d8aad;
    --bar-light: #a3c4d6;
    --bar-text: #ffffff;
    --screen-bg: #ffffff;
    --row-line: #d4d4d4;
    --title-ink: #1e1e1e;
    --item-ink: #3a3a3a;
    --accent: #4f86b4;
    --tick-fill: #6e9bbd;
    --tab-ink: #444444;
    --tab-active: #3f6f96;
  }
  * { box-sizing: border-box; margin: 0; padding: 0; }
  html, body { width: 1200px; height: 865px; overflow: hidden; }
  body {
    background: var(--page-bg);
    font-family: "Arimo", Arial, sans-serif;
    position: relative;
  }
  .screen {
    position: absolute;
    left: 400px; top: 70px;
    width: 400px; height: 725px;
    background: var(--screen-bg);
    border: 1px solid #dcdfe3;
    overflow: hidden;
    display: flex; flex-direction: column;
  }
  .top-bar {
    height: 82px;
    background: linear-gradient(100deg, var(--bar-dark) 0%, var(--bar-light) 55%, var(--bar-dark) 100%);
    color: var(--bar-text);
    position: relative;
  }
  .status {
    display: flex; justify-content: space-between; align-items: center;
    height: 22px; padding: 0 8px;
    font-size: 12px;
  }
  .status .carrier { display: flex; align-items: center; gap: 3px; }
  .dot { width: 6px; height: 6px; border-radius: 50%; border: 1px solid var(--bar-text); }
  .dot.on { background: var(--bar-text); }
  .status .battery { display: flex; align-items: center; gap: 5px; }
  .nav {
    position: relative; height: 60px;
    display: flex; align-items: center; justify-content: center;
  }
  .nav .back {
    position: absolute; left: 10px; top: 50%; transform: translateY(-50%);
    display: flex; align-items: center; gap: 5px; font-size: 19px;
  }
  .nav .title { font-size: 24px; font-weight: 500; letter-spacing: 0.3px; }
  .list { flex: 1; }
  .list-heading {
    font-size: 22px; color: var(--title-ink); font-weight: 500;
    padding: 22px 16px 8px;
  }
  .row {
    height: 76px; border-top: 1px solid var(--row-line);
    display: flex; align-items: center; padding: 0 16px;
  }
  .row:last-child { border-bottom: 1px solid var(--row-line); }
  .row .name {
    flex: 1;
    font-family: "Roboto Condensed", "Arial Narrow", sans-serif;
    font-weight: 300; font-size: 40px; color: var(--item-ink);
  }
  .row .status-icon { margin-right: 14px; }
  .tab-bar {
    height: 66px; border-top: 1px solid #e2e2e2;
    display: flex; justify-content: space-around; align-items: center;
    font-size: 12px; color: var(--tab-ink);
  }
  .tab { display: flex; flex-direction: column; align-items: center; gap: 3px; width: 80px; }
  .tab.active { color: var(--tab-active); }
</style>
</head>
<body>
<main class="screen">
  <header class="top-bar">
    <div class="status">
      <span class="carrier">
        <span class="dot on"></span><span class="dot on"></span><span class="dot"></span><span class="dot"></span><span class="dot"></span>
        <span>&nbsp;VHR</span>
        <svg width="14" height="10" viewBox="0 0 14 10"><path d="M1 4 Q7 -1 13 4 M3.5 6 Q7 3 10.5 6 M7 9 L5.5 7.5 Q7 6.5 8.5 7.5 Z" fill="none" stroke="#fff" stroke-width="1.3"/></svg>
      </span>
      <span class="time">5:17 PM</span>
      <span class="battery">50 %
        <svg width="24" height="11" viewBox="0 0 24 11"><rect x="0.5" y="0.5" width="20" height="10" rx="2" fill="none" stroke="#fff"/><rect x="2" y="2" width="9" height="7" fill="#fff"/><rect x="21.5" y="3.5" width="2" height="4" fill="#fff"/></svg>
      </span>
    </div>
    <nav class="nav">
      <span class="back">
        <svg width="12" height="20" viewBox="0 0 12 20"><path d="M10 2 L2 10 L10 18" fill="none" stroke="#fff" stroke-width="2.5"/></svg>
        Back
      </span>
      <h1 class="title">Objectives</h1>
    </nav>
  </header>

  <section class="list">
    <h2 class="list-heading">Select An Objective:</h2>
    <div class="row"><span class="name">Objective#1</span>
      <svg class="status-icon" width="26" height="26" viewBox="0 0 26 26"><circle cx="13" cy="13" r="12" fill="var(--tick-fill)"/><path d="M8 13 L12 16 L13 9" fill="none" stroke="#fff" stroke-width="1.6"/></svg>
      <svg width="12" height="20" viewBox="0 0 12 20"><path d="M2 2 L10 10 L2 18" fill="none" stroke="var(--accent)" stroke-width="1.6"/></svg>
    </div>
    <div class="row"><span class="name">Objective#2</span>
      <svg class="status-icon" width="26" height="26" viewBox="0 0 26 26"><circle cx="13" cy="13" r="12" fill="var(--tick-fill)"/><path d="M8 13 L12 16 L13 9" fill="none" stroke="#fff" stroke-width="1.6"/></svg>
      <svg width="12" height="20" viewBox="0 0 12 20"><path d="M2 2 L10 10 L2 18" fill="none" stroke="var(--accent)" stroke-width="1.6"/></svg>
    </div>
    <div class="row"><span class="name">Objective#3</span>
      <svg class="status-icon" width="26" height="26" viewBox="0 0 26 26"><circle cx="13" cy="13" r="11.5" fill="none" stroke="var(--accent)" stroke-width="1.6"/></svg>
      <svg width="12" height="20" viewBox="0 0 12 20"><path d="M2 2 L10 10 L2 18" fill="none" stroke="var(--accent)" stroke-width="1.6"/></svg>
    </div>
    <div class="row"><span class="name">Objective#4</span>
      <svg class="status-icon" width="26" height="26" viewBox="0 0 26 26"><circle cx="13" cy="13" r="12" fill="var(--tick-fill)"/><path d="M8 13 L12 16 L13 9" fill="none" stroke="#fff" stroke-width="1.6"/></svg>
      <svg width="12" height="20" viewBox="0 0 12 20"><path d="M2 2 L10 10 L2 18" fill="none" stroke="var(--accent)" stroke-width="1.6"/></svg>
    </div>
    <div class="row"><span class="name">Objective#5</span>
      <svg class="status-icon" width="26" height="26" viewBox="0 0 26 26"><circle cx="13" cy="13" r="11.5" fill="none" stroke="var(--accent)" stroke-width="1.6"/></svg>
      <svg width="12" height="20" viewBox="0 0 12 20"><path d="M2 2 L10 10 L2 18" fill="none" stroke="var(--accent)" stroke-width="1.6"/></svg>
    </div>
  </section>

  <footer class="tab-bar">
    <div class="tab">
      <svg width="30" height="26" viewBox="0 0 30 26"><path d="M3 13 L15 3 L27 13 M6 11 V24 H24 V11 M12 24 V16 H18 V24" fill="none" stroke="currentColor" stroke-width="1.4"/></svg>
      <span>Home</span>
    </div>
    <div class="tab active">
      <svg width="30" height="26" viewBox="0 0 30 26"><circle cx="15" cy="13" r="11" fill="none" stroke="currentColor" stroke-width="1.4" stroke-dasharray="14 3"/><circle cx="15" cy="13" r="6" fill="none" stroke="currentColor" stroke-width="1.4"/></svg>
      <span>Obejectives</span>
    </div>
    <div class="tab">
      <svg width="30" height="26" viewBox="0 0 30 26"><rect x="3" y="4" width="24" height="19" fill="none" stroke="currentColor" stroke-width="1.4"/><path d="M6 8 H24 M6 12 H14 M6 15 H14 M6 18 H14 M17 12 H24 M17 15 H24 M17 18 H24" stroke="currentColor" stroke-width="1.2"/></svg>
      <span>News</span>
    </div>
    <div class="tab">
      <svg width="30" height="26" viewBox="0 0 30 26"><path d="M20 8 V4 H4 V22 H20 V18 M12 13 H27 M23 9 L27 13 L23 17" fill="none" stroke="currentColor" stroke-width="1.4"/></svg>
      <span>Logout</span>
    </div>
  </footer>
</main>
</body>
</html>
```